Flyer for Commercial Roofing Company

We are seeking a talented graphic designer to create a high-quality, visually appealing bifold brochure for Brackenvale Roofing, a certified commercial roofing company specializing in apartment communities. The brochure will be 8.5x11 inches when folded and 17x11 inches when open, containing a front cover, two inside pages, and a back cover. The content is already developed, highlighting our services, key features, and contact information. The design should incorporate professional imagery of multifamily properties, modern icons, a clean layout, and our brand colors and logo to convey trust, expertise, and innovation. The goal is to produce a compelling marketing piece that engages property managers and decision-makers.
Target Market(s)
Apartment Communites
Look and feel
Each slider illustrates characteristics of the customer's brand and the style your logo design should communicate.

```html
<!DOCTYPE html>
<html lang="en">
<head>
<meta charset="utf-8">
<title>Brackenvale Roofing Bifold Brochure</title>
<link rel="stylesheet" href="https://fonts.googleapis.com/css2?family=Poppins:wght@400;500;600;700;800&family=Oswald:wght@600;700&display=swap">
<style>
:root{
  --navy:#2d3392;
  --red:#a0141b;
  --red-dark:#7c0d12;
  --ink:#1a1a1a;
  --paper:#ffffff;
  --backdrop:#c9c9cb;
  --rule:#b9bcc8;
}
*{box-sizing:border-box;margin:0;padding:0}
html,body{width:1200px;height:2400px;overflow:hidden}
body{background:var(--backdrop);font-family:'Poppins',sans-serif;color:var(--ink);position:relative}
.spread{position:absolute;left:40px;width:1024px;height:662px;background:var(--paper);transform:scale(1.09375);transform-origin:0 0;overflow:hidden}
.spread--outer{top:436px}
.spread--inner{top:1240px}
.abs{position:absolute}
.photo{position:absolute}
.brand{position:absolute;display:flex;align-items:center;gap:8px;font-weight:700;color:var(--navy);white-space:nowrap}
.brand__mark{background:var(--navy);display:block}
/* outer spread */
.accent-bar{left:70px;top:132px;width:740px;height:8px;background:var(--red)}
.red-block{left:0;top:140px;width:58px;height:272px;background:var(--red)}
.testimonial-panel{left:70px;top:147px;width:442px;height:265px;background:var(--navy)}
.testimonial-photo{left:87px;top:163px;width:183px;height:230px;border:2px solid #fff;background:linear-gradient(160deg,#8fb6de 0%,#c9b9a4 45%,#5c8a3c 100%)}
.quote-mark{left:300px;top:150px;font-family:'Oswald',sans-serif;font-size:64px;font-weight:700;color:var(--red);line-height:1}
.quote-text{left:302px;top:195px;width:160px;font-size:12.5px;line-height:15px;color:#fff}
.quote-name{left:302px;top:270px;width:156px;text-align:right;font-size:12px;font-weight:700;color:#fff}
.quote-role{left:302px;top:286px;width:156px;text-align:right;font-size:8.5px;color:#fff}
.quote-rule{left:302px;top:306px;width:170px;height:1px;background:#7a80c4}
.touch-title{left:302px;top:328px;font-size:12.5px;font-weight:700;color:#fff}
.touch-text{left:302px;top:347px;width:175px;font-size:9px;line-height:11px;color:#fff}
.house-photo{left:512px;top:147px;width:410px;height:265px;background:linear-gradient(180deg,#7fb0e6 0%,#cfe2f2 40%,#9aa0ad 60%,#4f8a34 85%,#3d7428 100%)}
.cover-tower{left:925px;top:30px;width:99px;height:370px;background:var(--navy)}
.cover-wedge{left:890px;top:330px;width:134px;height:82px}
.contact{left:60px;top:420px;width:395px;text-align:center}
.contact__title{font-size:15px;font-weight:700;color:var(--ink);letter-spacing:.3px}
.contact__title span{color:var(--navy)}
.contact__line{display:flex;flex-direction:column;align-items:center;font-size:11px;margin-top:6px}
.contact__line svg{margin-bottom:3px}
.contact__cta{font-size:17px;font-weight:800;color:var(--red);margin-top:12px;line-height:18px}
.contact__sub{font-size:17px;line-height:20px}
.headline{left:563px;top:430px}
.headline__small{font-size:17px;font-weight:800;line-height:20px;letter-spacing:.3px}
.headline__big{font-family:'Oswald',sans-serif;font-weight:700;font-size:41px;color:var(--red);line-height:46px;letter-spacing:.5px;transform:scaleX(.92);transform-origin:left}
.trust-shield{left:910px;top:422px}
.features{left:563px;top:545px;display:flex;gap:16px}
.feature{display:flex;align-items:center;gap:6px;font-size:11.5px;font-weight:700;line-height:13px}
.cover-url{left:565px;top:597px;font-size:14px;font-weight:700;letter-spacing:.5px}
.cover-url span{color:var(--navy)}
/* inner spread */
.why-panel{left:0;top:0;width:512px;height:205px;background:var(--navy)}
.why-title{left:55px;top:43px;font-size:13px;font-weight:700;color:#fff}
.why-text{left:55px;top:65px;width:320px;font-size:10px;line-height:12px;color:#fff}
.why-cards{left:53px;top:140px;width:414px;height:105px;border-radius:6px;overflow:hidden;display:flex}
.why-card{flex:1;background:var(--red);color:#fff;text-align:center;padding-top:20px;position:relative}
.why-card--mid{background:var(--red-dark)}
.why-card__title{font-size:10px;font-weight:700;line-height:12px}
.why-card__text{font-size:8.5px;line-height:10px;margin-top:6px}
.why-icon{top:125px;width:28px;height:28px;border-radius:50%;background:#fff;border:2px solid var(--navy)}
.section-title{font-size:13px;font-weight:700;color:var(--ink)}
.section-title span{color:var(--navy)}
.solutions-title{left:55px;top:262px}
.list-item{position:absolute;display:flex;align-items:center}
.list-item__photo{position:relative;flex:none;width:82px;height:50px}
.list-item__rule{flex:none;width:2px;height:48px;background:var(--navy);margin:0 20px 0 9px}
.list-item__name{font-size:10.5px;font-weight:700;color:var(--red)}
.list-item__text{font-size:9px;line-height:11px;width:250px}
.services-title{left:572px;top:43px}
.services-text{left:572px;top:67px;width:270px;font-size:10.5px;line-height:12px}
.service{position:absolute;left:572px;display:flex;align-items:center}
.service__photo{position:relative;flex:none;width:84px;height:72px}
.service__rule{flex:none;width:2px;height:72px;background:var(--navy);margin:0 20px 0 7px}
.service__name{font-size:13px;font-weight:700;color:var(--red);line-height:15px}
.service__text{font-size:9.5px;line-height:11px;margin-top:3px;width:140px}
.side-photo{left:865px;top:140px;width:135px;height:420px;background:linear-gradient(180deg,#2d3392 0%,#7d8aa8 35%,#d8dde3 60%,#c6a98a 100%)}
.side-band{left:1000px;top:30px;width:24px;height:530px;background:var(--navy)}
.footer-url{top:590px;width:150px;height:16px;background:var(--navy);color:#fff;font-size:8px;line-height:16px;padding-left:14px;clip-path:polygon(6px 0,100% 0,100% 100%,0 100%)}
.page-num{top:589px;width:18px;height:18px;border-radius:50%;background:#fff;border:1.5px solid var(--red);font-size:7px;text-align:center;line-height:15px;font-weight:600}
</style>
</head>
<body>

<section class="spread spread--outer" aria-label="Outer spread: back and front cover">
  <div class="brand" style="left:150px;top:70px;font-size:17px"><span class="brand__mark" style="width:16px;height:16px"></span>Brackenvale Roofing</div>
  <div class="brand" style="left:560px;top:62px;font-size:20px"><span class="brand__mark" style="width:18px;height:18px"></span>Brackenvale Roofing</div>

  <div class="abs accent-bar"></div>
  <div class="abs red-block"></div>
  <div class="abs testimonial-panel"></div>
  <div class="photo testimonial-photo" role="img" aria-label="Photo of a happy family in front of their home"></div>
  <div class="abs quote-mark">“</div>
  <p class="abs quote-text">Brackenvale Roofing’s expertise and professionalism made all the difference for our property.</p>
  <p class="abs quote-name">DANA R.</p>
  <p class="abs quote-role">Property Manager</p>
  <div class="abs quote-rule"></div>
  <p class="abs touch-title">Get in Touch</p>
  <p class="abs touch-text">Ready to protect your property with the best in roofing? Contact us today!</p>

  <div class="photo house-photo" role="img" aria-label="Photo of a modern two-storey residential building with lawn"></div>
  <div class="abs cover-tower"></div>
  <svg class="abs cover-wedge" viewBox="0 0 134 82" aria-hidden="true"><polygon points="0,82 134,0 134,82" fill="#a0141b"/></svg>

  <div class="abs contact">
    <p class="contact__title"><span>CONTACT</span> US TODAY!</p>
    <div class="contact__line">
      <svg width="14" height="14" viewBox="0 0 14 14"><circle cx="7" cy="7" r="6" fill="none" stroke="#2d3392" stroke-width="1.2"/><path d="M4.8 4 5.8 4 6.3 5.4 5.7 6a4 4 0 0 0 2.3 2.3l.6-.6 1.4.5v1A.8.8 0 0 1 9.2 10 5.4 5.4 0 0 1 4 4.8.8.8 0 0 1 4.8 4Z" fill="#a0141b"/></svg>
      555.014.2290</div>
    <div class="contact__line">
      <svg width="14" height="14" viewBox="0 0 14 14"><circle cx="7" cy="7" r="6" fill="none" stroke="#2d3392" stroke-width="1.2"/><rect x="4" y="4.8" width="6" height="4.4" fill="#a0141b"/><path d="M4 4.8 7 7.2 10 4.8" fill="none" stroke="#fff" stroke-width=".7"/></svg>
      sales@brackenvaleroofing.com</div>
    <div class="contact__line">
      <svg width="14" height="14" viewBox="0 0 14 14"><circle cx="7" cy="7" r="6" fill="none" stroke="#2d3392" stroke-width="1.2"/><circle cx="7" cy="7" r="3.3" fill="none" stroke="#a0141b" stroke-width=".8"/><path d="M3.7 7h6.6M7 3.7v6.6" stroke="#a0141b" stroke-width=".7"/></svg>
      www.brackenvaleroofing.com</div>
    <p class="contact__cta">REQUEST A FREE</p>
    <p class="contact__sub">Roof Inspection Today</p>
  </div>

  <div class="abs headline">
    <p class="headline__small">PROTECTING APARTMENT<br>COMMUNITIES WITH PRECISION</p>
    <p class="headline__big">ROOFING SOLUTIONS</p>
  </div>
  <svg class="abs trust-shield" width="88" height="108" viewBox="0 0 88 108" aria-hidden="true"><path d="M44 2 86 16V56C86 82 64 98 44 106 24 98 2 82 2 56V16Z" fill="#2d3392"/><path d="M44 9 79 21V56C79 78 61 92 44 99 27 92 9 78 9 56V21Z" fill="#fff"/></svg>

  <div class="abs features">
    <div class="feature"><svg width="22" height="22" viewBox="0 0 22 22"><circle cx="11" cy="11" r="10" fill="none" stroke="#2d3392" stroke-width="1.5"/><path d="M6.5 11.5 9.5 14.5 15.5 8" fill="none" stroke="#2d3392" stroke-width="1.5"/></svg>Certified<br>Expertise</div>
    <div class="feature"><svg width="22" height="22" viewBox="0 0 22 22"><circle cx="11" cy="11" r="10" fill="none" stroke="#2d3392" stroke-width="1.5"/><circle cx="11" cy="11" r="4.5" fill="none" stroke="#2d3392" stroke-width="1.3"/></svg>Unmatched<br>Reliability</div>
    <div class="feature"><svg width="22" height="22" viewBox="0 0 22 22"><circle cx="11" cy="11" r="10" fill="none" stroke="#2d3392" stroke-width="1.5"/><rect x="6.5" y="8" width="9" height="6" fill="none" stroke="#2d3392" stroke-width="1.2"/></svg>Industry-leading<br>Warranty</div>
  </div>
  <p class="abs cover-url">www.<span>brackenvaleroofing</span>.com</p>
</section>

<section class="spread spread--inner" aria-label="Inner spread: pages one and two">
  <div class="abs why-panel"></div>
  <h2 class="abs why-title">WHY CHOOSE BRACKENVALE ROOFING?</h2>
  <p class="abs why-text">We specialize in delivering superior roofing services tailored to meet the needs of apartment communities. Our certified experts ensure your property’s roof is built to last.</p>
  <div class="abs why-cards">
    <div class="why-card"><p class="why-card__title">Certified Roofing<br>Contractor</p><p class="why-card__text">Expert<br>craftsmanship<br>guaranteed.</p></div>
    <div class="why-card why-card--mid"><p class="why-card__title">20-Year<br>NDL Warranty</p><p class="why-card__text">Peace of<br>mind with long-term<br>protection</p></div>
    <div class="why-card"><p class="why-card__title">Vendor Credentialing<br>Compliance</p><p class="why-card__text">Approved<br>with all major<br>platforms.</p></div>
  </div>
  <div class="abs why-icon" style="left:103px"></div>
  <div class="abs why-icon" style="left:235px"></div>
  <div class="abs why-icon" style="left:376px"></div>

  <h3 class="abs section-title solutions-title">OUR ROOFING <span>SOLUTIONS</span></h3>
  <svg class="abs" style="left:250px;top:265px" width="220" height="300" viewBox="0 0 220 300" aria-hidden="true"><path d="M6 6H150L215 45V295H185" fill="none" stroke="#b9bcc8" stroke-width="1"/></svg>

  <div class="list-item" style="left:56px;top:290px"><div class="list-item__photo" role="img" aria-label="Photo of a worker on a flat TPO roof" style="background:linear-gradient(180deg,#c9d3df,#4a4f5a)"></div><span class="list-item__rule"></span><div><p class="list-item__name">TPO Roofing</p><p class="list-item__text">Energy-efficient and durable for large flat roofs.</p></div></div>
  <div class="list-item" style="left:56px;top:345px"><div class="list-item__photo" role="img" aria-label="Photo of an EPDM membrane roof" style="background:linear-gradient(180deg,#a57355,#d9c3a9)"></div><span class="list-item__rule"></span><div><p class="list-item__name">EPDM Roofing</p><p class="list-item__text">Resilient against extreme weather with proven longevity.</p></div></div>
  <div class="list-item" style="left:56px;top:400px"><div class="list-item__photo" role="img" aria-label="Photo of townhouse rooftops" style="background:linear-gradient(180deg,#8fb3df,#5a6f8d)"></div><span class="list-item__rule"></span><div><p class="list-item__name">PVC Roofing</p><p class="list-item__text">Fire, chemical, and water-resistant for multifamily properties.</p></div></div>
  <div class="list-item" style="left:56px;top:455px"><div class="list-item__photo" role="img" aria-label="Photo of an asphalt shingle roof" style="background:linear-gradient(180deg,#7d8794,#2c2f36)"></div><span class="list-item__rule"></span><div><p class="list-item__name">Asphalt Shingles</p><p class="list-item__text">Versatile and cost-effective with curb appeal.</p></div></div>
  <div class="list-item" style="left:56px;top:510px"><div class="list-item__photo" role="img" aria-label="Photo of a red coated metal roof" style="background:linear-gradient(180deg,#d9707a,#a72838)"></div><span class="list-item__rule"></span><div><p class="list-item__name">Roof Coatings</p><p class="list-item__text">Extend the lifespan of existing roofs and reduce maintenance costs.</p></div></div>

  <div class="brand" style="left:48px;top:590px;font-size:9px;gap:5px"><span class="brand__mark" style="width:10px;height:10px"></span>Brackenvale Roofing</div>
  <div class="abs footer-url" style="left:295px">www.brackenvaleroofing.com</div>
  <div class="abs page-num" style="left:441px">01</div>

  <h3 class="abs section-title services-title"><span>OUR SERVICES</span></h3>
  <p class="abs services-text">We offer comprehensive roofing solutions for every stage of your roof’s lifecycle.</p>

  <div class="service" style="top:115px"><div class="service__photo" role="img" aria-label="Photo of a roofer repairing a pitched roof" style="background:linear-gradient(180deg,#cfe0f0,#5a4a3e)"></div><span class="service__rule"></span><div><p class="service__name">Roof<br>Repairs</p><p class="service__text">Fast, reliable fixes to extend roof life.</p></div></div>
  <div class="service" style="top:200px"><div class="service__photo" role="img" aria-label="Photo of an inspector on a metal roof" style="background:linear-gradient(180deg,#9aa3ad,#3e444c)"></div><span class="service__rule"></span><div><p class="service__name">Roof<br>Inspections</p><p class="service__text">Thorough assessments to identify potential issues.</p></div></div>
  <div class="service" style="top:290px"><div class="service__photo" role="img" aria-label="Photo of a roofer maintaining a metal roof" style="background:linear-gradient(180deg,#6f7780,#2c3138)"></div><span class="service__rule"></span><div><p class="service__name">Preventative<br>Maintenance</p><p class="service__text">Keep your roof in optimal condition year-round.</p></div></div>
  <div class="service" style="top:380px"><div class="service__photo" role="img" aria-label="Photo of roofers installing a new roof" style="background:linear-gradient(180deg,#b7c9dd,#4d545c)"></div><span class="service__rule"></span><div><p class="service__name">New Roof<br>Installations</p><p class="service__text">High-quality installations with certified materials.</p></div></div>
  <div class="service" style="top:470px"><div class="service__photo" role="img" aria-label="Photo of an emergency roof repair on a house" style="background:linear-gradient(180deg,#9ec3ea,#7a5a48)"></div><span class="service__rule"></span><div><p class="service__name">Emergency<br>Services</p><p class="service__text">24/7 rapid response to urgent roofing issues.</p></div></div>

  <div class="abs side-band"></div>
  <div class="photo side-photo" role="img" aria-label="Photo of a couple walking in front of an apartment building"></div>

  <div class="brand" style="left:568px;top:590px;font-size:9px;gap:5px"><span class="brand__mark" style="width:10px;height:10px"></span>Brackenvale Roofing</div>
  <div class="abs footer-url" style="left:832px">www.brackenvaleroofing.com</div>
  <div class="abs page-num" style="left:978px">02</div>
</section>

</body>
</html>
```